Request for Business Card Design

Hi. My name is Marlene, I am looking for a new business card design for my company, Quarrow Signal Instruments, LLC. I really like the design you did for Tarsel Venture and was hoping you could do something similar using our full logo and our mark. I am also open to any raised texture design using our mark. I have attached our full logo, which would need to be somewhere on the card, as well as the mark in both outline and full form, as well as our brand colors / guide. The card does not have to be white, as long as our logo and mark appear. I actually like darker colored business cards more, but am open to all options. If you are interested in working with me, please let me know. We would also take the business card design into letterhead design if you can do that.

```html
<!DOCTYPE html>
<html lang="en">
<head>
<meta charset="utf-8">
<title>Quarrow Signal Instruments – Business Card</title>
<link rel="stylesheet" href="https://fonts.googleapis.com/css2?family=Barlow:wght@400;500;700&display=swap">
<style>
  :root {
    --backdrop: #7f97b8;
    --orange: #f07428;
    --orange-light: #f4914f;
    --blue: #2b9fc4;
    --blue-light: #3aaacd;
    --ink: #ffffff;
    --ink-soft: rgba(255,255,255,0.14);
  }
  * { box-sizing: border-box; margin: 0; padding: 0; }
  html, body { width: 1200px; height: 876px; overflow: hidden; }
  body {
    background: var(--backdrop);
    font-family: "Barlow", Arial, sans-serif;
    color: var(--ink);
    display: flex;
    align-items: center;
    justify-content: center;
    gap: 50px;
  }
  .card {
    position: relative;
    width: 520px;
    height: 297px;
    border-radius: 3px;
    overflow: hidden;
  }
  .card--front { background: linear-gradient(120deg, var(--orange-light), var(--orange) 65%); }
  .card--back { background: linear-gradient(120deg, var(--blue-light), var(--blue)); }

  .holder {
    position: absolute; top: 32px; left: 0; right: 0;
    text-align: center;
  }
  .holder__name { font-size: 19px; letter-spacing: 1.5px; text-transform: uppercase; }
  .holder__name strong { font-weight: 700; }
  .holder__name span { font-weight: 400; }
  .holder__role { font-size: 13px; margin-top: 1px; }

  .brand {
    display: flex; align-items: center; gap: 10px;
    font-weight: 700; text-transform: uppercase;
  }
  .brand__dot { width: 14px; height: 14px; border-radius: 50%; background: var(--ink); flex: none; }
  .brand__name { line-height: 1; }
  .brand--front { position: absolute; top: 100px; left: 0; right: 0; justify-content: center; }
  .brand--front .brand__name { font-size: 24px; letter-spacing: 2px; }

  .contacts {
    position: absolute; left: 20px; right: 20px; bottom: 26px;
    display: flex; align-items: flex-start;
  }
  .contact {
    flex: 1; display: flex; flex-direction: column; align-items: center; gap: 8px;
    font-size: 13px; text-align: center; line-height: 1.3;
  }
  .contact svg { width: 18px; height: 18px; }
  .contacts__rule { width: 1px; height: 50px; background: var(--ink); opacity: 0.8; margin-top: 6px; }

  .brand--back { position: absolute; top: 62px; left: 40px; }
  .brand--back .brand__dot { width: 22px; height: 22px; }
  .brand--back .brand__name { font-size: 34px; letter-spacing: 3px; }
  .backdrop-disc {
    position: absolute; right: -40px; bottom: -90px;
    width: 280px; height: 280px; border-radius: 50%;
    background: var(--ink-soft);
  }
</style>
</head>
<body>
  <section class="card card--front" aria-label="Business card front">
    <div class="holder">
      <p class="holder__name"><strong>Marlene</strong> <span>Hartwell</span></p>
      <p class="holder__role">Director</p>
    </div>
    <div class="brand brand--front">
      <span class="brand__dot"></span>
      <span class="brand__name">Quarrow Signal Instruments</span>
    </div>
    <div class="contacts">
      <div class="contact">
        <svg viewBox="0 0 20 20" aria-hidden="true"><circle cx="10" cy="10" r="10" fill="#fff"/><rect x="7" y="5" width="6" height="10" rx="1" fill="none" stroke="#f07428" stroke-width="1.5"/></svg>
        <span>+000 55501 2468</span>
      </div>
      <div class="contacts__rule"></div>
      <div class="contact">
        <svg viewBox="0 0 20 20" aria-hidden="true"><circle cx="10" cy="10" r="10" fill="#fff"/><path d="M10 4.5a3.5 3.5 0 0 0-3.5 3.5c0 2.6 3.5 6.5 3.5 6.5s3.5-3.9 3.5-6.5A3.5 3.5 0 0 0 10 4.5z" fill="#f07428"/><circle cx="10" cy="8" r="1.2" fill="#fff"/></svg>
        <span>Street Address Here<br>Leyton Bay, 4410</span>
      </div>
      <div class="contacts__rule"></div>
      <div class="contact">
        <svg viewBox="0 0 20 20" aria-hidden="true"><circle cx="10" cy="10" r="10" fill="#fff"/><rect x="5" y="6.5" width="10" height="7" fill="none" stroke="#f07428" stroke-width="1.4"/><path d="M5 6.5l5 4 5-4" fill="none" stroke="#f07428" stroke-width="1.4"/></svg>
        <span>hello@quarrow.test</span>
      </div>
    </div>
  </section>

  <section class="card card--back" aria-label="Business card back">
    <div class="backdrop-disc"></div>
    <div class="brand brand--back">
      <span class="brand__dot"></span>
      <span class="brand__name">Quarrow</span>
    </div>
  </section>
</body>
</html>
```